Veldmark Supplies Business Card

Professional business card that stand out to our potential customers. Front and back with clean modern design

Industry/Entity Type

Oil and gas

Contact Information for Business Card

Name, address, website , office phone and cell number

Requirements
Must have
• Editable files for each employee

```html
<!DOCTYPE html>
<html lang="en">
<head>
<meta charset="utf-8">
<title>Veldmark Supplies Business Card</title>
<link href="https://fonts.googleapis.com/css2?family=Montserrat:wght@400;500;800&display=swap" rel="stylesheet">
<style>
  :root {
    --brand-red: #ec2027;
    --brand-blue: #00b0d4;
    --ink: #1c1c1c;
    --paper: #ffffff;
    --backdrop: #2a2a2a;
  }
  * { box-sizing: border-box; margin: 0; padding: 0; }
  html, body { width: 1200px; height: 880px; overflow: hidden; }
  body {
    background: var(--backdrop);
    font-family: "Montserrat", sans-serif;
    position: relative;
  }
  .card {
    position: absolute;
    width: 665px;
    height: 380px;
    overflow: hidden;
    box-shadow: 0 10px 24px rgba(0,0,0,0.45);
  }
  .card-front {
    left: 140px; top: 40px;
    background: var(--brand-red);
    display: flex; align-items: center; justify-content: center; gap: 16px;
  }
  .front-mark { width: 44px; height: 44px; background: var(--paper); }
  .front-name {
    color: var(--paper);
    font-weight: 800;
    font-size: 40px;
    letter-spacing: 1px;
    text-transform: uppercase;
  }
  .card-back {
    left: 395px; top: 460px;
    background: var(--paper);
  }
  .back-brand {
    position: absolute; left: 28px; top: 152px;
    display: flex; align-items: center; gap: 8px;
  }
  .back-mark { width: 22px; height: 22px; background: var(--brand-red); }
  .back-name {
    color: var(--brand-red);
    font-weight: 800; font-size: 18px;
    text-transform: uppercase; letter-spacing: 0.3px;
    white-space: nowrap;
  }
  .divider-lines { position: absolute; left: 300px; top: 40px; }
  .contact {
    position: absolute; left: 370px; top: 40px;
    color: var(--ink);
  }
  .person-name {
    color: var(--brand-red); font-weight: 800; font-size: 24px;
    text-transform: uppercase; line-height: 1.1; white-space: nowrap;
  }
  .person-title { font-size: 14px; margin-bottom: 14px; }
  .address { font-size: 14px; line-height: 1.3; margin-bottom: 12px; margin-left: 18px; }
  .contact-list { list-style: none; margin-left: 18px; }
  .contact-list li {
    display: flex; align-items: center; gap: 8px;
    font-size: 14px; line-height: 1.65; white-space: nowrap;
  }
  .contact-list .accent { color: var(--brand-red); }
  .icon { width: 17px; height: 17px; flex: none; }
  .footer-bands { position: absolute; left: 0; bottom: 0; }
  .footer-web {
    position: absolute; right: 22px; bottom: 22px;
    color: var(--paper); font-size: 15px; font-weight: 500;
  }
</style>
</head>
<body>

<section class="card card-front" aria-label="Card front">
  <span class="front-mark"></span>
  <span class="front-name">Veldmark Supplies</span>
</section>

<section class="card card-back" aria-label="Card back">
  <div class="back-brand">
    <span class="back-mark"></span>
    <span class="back-name">Veldmark Supplies</span>
  </div>

  <svg class="divider-lines" width="70" height="240" viewBox="0 0 70 240" aria-hidden="true">
    <line x1="8" y1="10" x2="60" y2="230" stroke="var(--brand-blue)" stroke-width="1.5"/>
    <line x1="30" y1="40" x2="58" y2="170" stroke="var(--brand-red)" stroke-width="1.5"/>
    <line x1="4" y1="70" x2="34" y2="200" stroke="var(--brand-red)" stroke-width="1.5"/>
  </svg>

  <div class="contact">
    <h1 class="person-name">Dara Whitlock</h1>
    <p class="person-title">President</p>
    <p class="address">2740 Harlow Ave, Ste<br>210, Dallas, TX 75204</p>
    <ul class="contact-list">
      <li>
        <svg class="icon" viewBox="0 0 18 18" aria-hidden="true"><rect width="18" height="18" rx="3" fill="var(--brand-red)"/><path d="M4 7c0-2 10-2 10 0v1h-3V7H7v1H4zM5 9h8l1 5H4z" fill="#fff"/></svg>
        <span>913-555-0147</span>
      </li>
      <li>
        <svg class="icon" viewBox="0 0 18 18" aria-hidden="true"><rect width="18" height="18" rx="3" fill="var(--brand-red)"/><rect x="6" y="3" width="6" height="12" rx="1" fill="none" stroke="#fff" stroke-width="1.4"/></svg>
        <span>000-000-9999</span>
      </li>
      <li>
        <svg class="icon" viewBox="0 0 18 18" aria-hidden="true"><rect width="18" height="18" rx="3" fill="var(--brand-red)"/><rect x="3" y="5" width="12" height="8" fill="none" stroke="#fff" stroke-width="1.3"/><path d="M3 5l6 5 6-5" fill="none" stroke="#fff" stroke-width="1.3"/></svg>
        <span>info@example-<span class="accent">youremail</span>.com</span>
      </li>
      <li>
        <svg class="icon" viewBox="0 0 18 18" aria-hidden="true"><rect width="18" height="18" rx="3" fill="var(--brand-red)"/><circle cx="9" cy="9" r="5" fill="none" stroke="#fff" stroke-width="1.3"/><path d="M4 9h10M9 4c-3 3-3 7 0 10M9 4c3 3 3 7 0 10" fill="none" stroke="#fff" stroke-width="1"/></svg>
        <span>www.<span class="accent">example-yourwebsite</span>.com</span>
      </li>
    </ul>
  </div>

  <svg class="footer-bands" width="665" height="70" viewBox="0 0 665 70" aria-hidden="true">
    <polygon points="0,52 420,40 416,70 0,70" fill="var(--brand-blue)"/>
    <polygon points="432,0 665,0 665,70 420,70" fill="var(--brand-red)"/>
  </svg>
  <p class="footer-web">www.example-web.com</p>
</section>

</body>
</html>
```